Business Cards for a law firm

Business cards for our law firm. Use our silhoette logo and OAK PARTNERS - check our website (www.oakpartners.example)

Contact Information for Business Card

our silhouette logo, OAK PARTNERS, 800-555-0147, Dorian Pemberton, dorian@oakpartners.example

Requirements
Must have
• our silhouette logo, OAK PARTNERS, 800-555-0147, Dorian Pemberton, dorian@oakpartners.example

```html
<!DOCTYPE html>
<html lang="en">
<head>
<meta charset="utf-8">
<title>Oak Partners – Business Cards</title>
<link rel="stylesheet" href="https://fonts.googleapis.com/css2?family=Cinzel:wght@500;700&family=Arimo:wght@400&display=swap">
<style>
  :root {
    --stage: #3a3a3a;
    --card-dark: #2f2f2f;
    --navy: #1b3270;
    --paper: #ffffff;
    --swoosh-shadow: #2a2a2a;
    --ink-light: #ffffff;
  }
  * { box-sizing: border-box; margin: 0; padding: 0; }
  html, body { width: 1200px; height: 689px; overflow: hidden; }
  body { background: var(--stage); position: relative; }

  .card {
    position: absolute;
    top: 196px;
    width: 520px;
    height: 297px;
    border-radius: 18px;
    overflow: hidden;
    box-shadow: 0 14px 30px rgba(0,0,0,.35);
  }

  /* Back of card */
  .card--back { left: 50px; background: var(--card-dark); }
  .card--back .brand-mark {
    position: absolute; left: 0; right: 0; top: 112px;
    display: flex; justify-content: center; align-items: center; gap: 12px;
    font-family: "Cinzel", serif; font-weight: 700; font-size: 30px;
    letter-spacing: 3px; color: var(--ink-light);
  }
  .card--back .brand-mark .dot {
    width: 14px; height: 14px; background: var(--ink-light);
  }
  .card--back .website {
    position: absolute; left: 0; right: 0; top: 196px; text-align: center;
    font-family: "Arimo", sans-serif; font-size: 14px; color: var(--ink-light);
  }

  /* Front of card */
  .card--front { left: 630px; background: var(--paper); }
  .card--front .swoosh { position: absolute; inset: 0; }
  .card--front .wordmark {
    position: absolute; left: 28px; top: 128px;
    display: flex; align-items: center; gap: 10px;
    font-family: "Cinzel", serif; font-weight: 700; font-size: 23px;
    letter-spacing: 2px; color: var(--navy);
  }
  .card--front .wordmark .dot { width: 13px; height: 13px; background: var(--navy); }

  .contact {
    position: absolute; right: 20px; top: 172px; text-align: right;
    color: var(--ink-light); font-family: "Arimo", sans-serif;
  }
  .contact .person {
    font-family: "Cinzel", serif; font-weight: 700; font-size: 16px;
    letter-spacing: 0.5px; margin-bottom: 7px;
  }
  .contact .line {
    display: flex; justify-content: flex-end; align-items: center; gap: 7px;
    font-size: 12px; line-height: 18px;
  }
  .contact .line svg { width: 11px; height: 11px; fill: var(--ink-light); }
</style>
</head>
<body>

<section class="card card--back" aria-label="Card back">
  <div class="brand-mark"><span class="dot"></span>OAK PARTNERS</div>
  <p class="website">www.oakpartners.example</p>
</section>

<section class="card card--front" aria-label="Card front">
  <svg class="swoosh" viewBox="0 0 520 297" preserveAspectRatio="none" aria-hidden="true">
    <path d="M140 297 C 240 297, 262 150, 468 0" fill="none" stroke="var(--swoosh-shadow)" stroke-width="7"/>
    <path d="M150 297 C 250 297, 270 150, 474 0 L520 0 L520 297 Z" fill="var(--navy)"/>
  </svg>

  <div class="wordmark"><span class="dot"></span>OAK PARTNERS</div>

  <div class="contact">
    <p class="person">Dorian Pemberton</p>
    <p class="line">800-555-0147
      <svg viewBox="0 0 24 24"><path d="M6.6 10.8a15.1 15.1 0 0 0 6.6 6.6l2.2-2.2a1 1 0 0 1 1-.25 11.4 11.4 0 0 0 3.6.57 1 1 0 0 1 1 1V20a1 1 0 0 1-1 1A17 17 0 0 1 3 4a1 1 0 0 1 1-1h3.5a1 1 0 0 1 1 1c0 1.25.2 2.45.57 3.57a1 1 0 0 1-.25 1z"/></svg>
    </p>
    <p class="line">dorian@oakpartners.example
      <svg viewBox="0 0 24 24"><path d="M2 5h20v14H2z M3 6l9 7 9-7" fill="var(--ink-light)" stroke="var(--navy)" stroke-width="1.5"/></svg>
    </p>
    <p class="line">www.oakpartners.example
      <svg viewBox="0 0 24 24"><circle cx="12" cy="12" r="10"/><path d="M2 12h20M12 2c3 3 3 17 0 20M12 2c-3 3-3 17 0 20" fill="none" stroke="var(--navy)" stroke-width="1.5"/></svg>
    </p>
  </div>
</section>

</body>
</html>
```